Coral Slumber Depot Website

Need a design for a local Miami mattress store.
The store is called Coral Slumber Depot.
need it to be something that customers can find on the internet and will
give them my location, they need to know i have the same brand mattress as the other store except i have them at almost half the price.

the office phone number is (786)413-9067
the office address is: 24517 sw Heron Glade Ln, Miami FL 33189

included is the logo, id like to stick the with white and teal design

here are is an excerpt that can or cannot be included

"We are a premium mattress discount outlet store located in South Florida; offering Free Delivery to Broward Miami-Dade, the Keys, and Palm Beach.

We carry the best brands in the market: Kellard DreamLoft; Brodin SpineEase, Whitcombe & Lyle, Pardue, among others.

We are open 7 days a week, and we are accessible from all major highways. We are a family business and our goal is to provide you with the most comfortable and best quality mattress at a price that has no competition. Come visit us and take a look at our large inventory selection."

```html
<!DOCTYPE html>
<html lang="en">
<head>
<meta charset="utf-8">
<title>Coral Slumber Depot</title>
<link href="https://fonts.googleapis.com/css2?family=Montserrat:wght@400;500;600&family=Lato:wght@300;400;700&display=swap" rel="stylesheet">
<style>
:root{
  --teal:#0a9eb0;
  --teal-dark:#0a7f8a;
  --teal-light:#92d3d2;
  --cream:#f4f2e6;
  --ink:#3a3a3a;
  --muted:#777;
  --card:#dcdcdc;
  --footer:#5a5a5a;
  --footer-dark:#2a2a2a;
  --gold:#f0b400;
}
*{box-sizing:border-box;margin:0;padding:0}
html,body{width:1200px;height:2320px;overflow:hidden;background:#fff}
body{position:relative;font-family:"Lato",sans-serif;color:var(--ink)}
.abs{position:absolute}
.topbar{left:0;top:0;width:1200px;height:64px;background:linear-gradient(#13a7b5,#0a8f9c)}
.topbar a{position:absolute;top:21px;color:#fff;font-size:20px;text-decoration:none;font-family:"Lato",sans-serif;white-space:nowrap}
.cart{left:1026px;top:14px;width:38px;height:38px;background:var(--teal);border:1px solid #6dd0da}
.cart-count{left:1052px;top:6px;width:20px;height:20px;border-radius:50%;background:var(--teal);border:2px solid #fff;color:#fff;font-size:11px;text-align:center;line-height:16px;font-weight:700}
.header{left:0;top:64px;width:1200px;height:115px;background:var(--cream);box-shadow:0 3px 6px rgba(0,0,0,.12)}
.brand{left:128px;top:104px;display:flex;align-items:center;gap:10px;font-family:"Montserrat",sans-serif;font-size:22px;font-weight:500;color:var(--teal-dark);white-space:nowrap}
.brand-mark{width:22px;height:22px;background:var(--teal)}
.nav a{position:absolute;top:116px;font-family:"Montserrat",sans-serif;font-size:24px;color:var(--teal);text-decoration:none;white-space:nowrap}
.nav a.current{color:#f26a2e}
.hero{left:128px;top:192px;width:945px;height:348px;background:var(--cream);border:1px solid #ddd;overflow:hidden}
.hero-text{left:560px;top:50px;width:370px;text-align:center;font-size:20px;line-height:30.5px;color:#444;white-space:nowrap}
.btn-shop{left:664px;top:248px;width:192px;height:48px;border-radius:4px;background:var(--teal-dark);color:#fff;font-family:"Montserrat",sans-serif;font-size:26px;font-weight:500;text-align:center;line-height:46px}
.dots{left:24px;top:312px;display:flex;gap:6px}
.dots i{width:9px;height:9px;border-radius:50%;border:1.5px solid #fff;display:block}
.dots i.on{background:#fff}
.section-title{position:absolute;left:126px;font-size:19px;color:#444;display:flex;align-items:center;width:946px;font-weight:400}
.section-title::after{content:"";flex:1;height:10px;margin-left:12px;background:repeating-linear-gradient(#fff 0 2px,#ddd 2px 3px)}
.card{position:absolute;width:197px;height:240px;background:var(--card);border:1px solid #bbb;border-radius:2px}
.card.sm{width:181px;height:221px}
.card .photo{position:absolute;left:9px;top:9px;right:9px;height:154px;background:radial-gradient(ellipse at 50% 55%,#e6dcc6 0 40%,#fff 72%);border:1px solid #eee}
.card.sm .photo{height:140px}
.card .name{position:absolute;left:11px;top:172px;font-size:13px;color:#666}
.card.sm .name{top:156px;font-size:12px}
.card .stars{position:absolute;right:11px;top:170px;font-size:11px;color:var(--gold);letter-spacing:1px}
.card.sm .stars{top:154px}
.card .add{position:absolute;left:6px;top:205px;width:99px;height:27px;background:linear-gradient(#1bb8cc,#0a97a8);border-radius:3px;color:#fff;font-size:11px;font-weight:700;text-align:center;line-height:27px}
.card.sm .add{top:187px;width:92px;height:25px;line-height:25px;font-size:10px}
.card .price{position:absolute;right:8px;top:207px;height:22px;padding:0 4px;background:#fff;border:1px solid #888;font-size:12px;font-weight:700;line-height:20px;letter-spacing:2px}
.card.sm .price{top:189px}
.brand-logo{position:absolute;top:1120px;font-family:"Lato",sans-serif;font-weight:700;font-size:20px;color:#2c4f8a;text-align:center;white-space:nowrap}
.tab{position:absolute;left:128px;width:182px;height:50px;background:#f2f2f2;border-top:3px solid #d6d6d6;color:var(--teal);font-size:27px;text-align:center;line-height:46px}
.tab.active{background:var(--teal);color:#fff;border:none;line-height:50px}
.page{position:absolute;top:1659px;width:36px;height:34px;background:linear-gradient(#eee,#d3d3d3);border:1px solid #c8c8c8;border-radius:3px;font-size:14px;text-align:center;line-height:32px;color:#555}
.page.on{background:var(--teal);color:#fff;border-color:var(--teal)}
.features{left:0;top:1846px;width:1200px;height:142px;background:var(--cream);border-bottom:6px solid #e4dfc8}
.feature{position:absolute;top:30px;width:290px}
.feature h4{font-family:"Montserrat",sans-serif;font-size:12px;letter-spacing:1px;color:#6b6550;font-weight:600;padding-left:22px;position:relative;line-height:16px}
.feature h4::before{content:"";position:absolute;left:0;top:0;width:15px;height:15px;border-radius:50%;background:#8c8568}
.feature p{margin-top:6px;padding-left:22px;font-size:12px;line-height:22px;color:#9b9478;white-space:nowrap}
.footer{left:0;top:1994px;width:1200px;height:297px;background:var(--footer);color:#fff}
.footer-title{position:absolute;font-size:19px;font-weight:700;color:#111;white-space:nowrap}
.field{position:absolute;left:187px;width:160px;height:27px;background:#fff;border:2px solid #ccc;border-radius:3px;font-size:12px;font-style:italic;color:#666;padding:5px 10px}
.submit{left:190px;top:2160px;width:60px;height:24px;background:var(--teal);color:#fff;font-size:12px;text-align:center;line-height:24px}
.contact-line{position:absolute;left:512px;font-size:19px;color:#fff;line-height:24px;white-space:nowrap}
.social{position:absolute;left:831px;display:flex;align-items:center;gap:12px;font-size:13px;color:#fff;white-space:nowrap}
.social i{width:20px;height:20px;border-radius:50%;background:#fff;display:block}
.social.on{color:#2fc1d8}
.social.on i{background:#2fc1d8}
.bottombar{left:0;top:2291px;width:1200px;height:29px;background:var(--footer-dark);color:#ddd;font-size:9px}
.bottombar span{white-space:nowrap}
</style>
</head>
<body>

<div class="abs topbar">
  <a style="left:797px">My Account</a>
  <a style="left:940px">Checkout</a>
</div>
<div class="abs cart"><svg width="38" height="38" viewBox="0 0 38 38"><path d="M10 15h18l-2 11H12z" fill="none" stroke="#fff" stroke-width="2"/><path d="M14 15l5-6 5 6" fill="none" stroke="#fff" stroke-width="2"/></svg></div>
<div class="abs cart-count">0</div>

<header class="abs header"></header>
<div class="abs brand"><span class="brand-mark"></span>Coral Slumber Depot</div>
<nav class="nav">
  <a class="current" style="left:466px">Home</a>
  <a style="left:565px">Products</a>
  <a style="left:699px">Prices</a>
  <a style="left:798px">About Us</a>
  <a style="left:938px">Contact Us</a>
</nav>

<section class="abs hero">
  <svg class="abs" style="left:0;top:0" width="945" height="348">
    <defs><linearGradient id="bedroom" x1="0" y1="0" x2="1" y2="1"><stop offset="0" stop-color="#6b4a34"/><stop offset=".5" stop-color="#b49578"/><stop offset="1" stop-color="#4a3426"/></linearGradient></defs>
    <polygon points="0,0 480,0 592,285 0,285" fill="url(#bedroom)" role="img" aria-label="Photo of a hotel-style bedroom with a made double bed"/>
    <polygon points="0,285 592,285 672,348 0,348" fill="var(--teal-light)"/>
  </svg>
  <div class="abs dots"><i></i><i class="on"></i><i></i><i></i><i></i></div>
  <p class="abs hero-text">We are a premium mattress<br>discount outlet store located in<br>South Florida; offering Free<br>Delivery to Broward Miami-Dade,<br>the Keys, and Palm Beach</p>
  <div class="abs btn-shop">Shop now</div>
</section>

<h2 class="section-title" style="top:594px">Featured Products</h2>
<div class="card" style="left:157px;top:686px"><div class="photo" role="img" aria-label="Mattress product photo"></div><span class="name">Product Name</span><span class="stars">★★★</span><span class="add">ADD TO CART</span><span class="price">$200</span></div>
<div class="card" style="left:386px;top:686px"><div class="photo" role="img" aria-label="Mattress product photo"></div><span class="name">Product Name</span><span class="stars">★★★</span><span class="add">ADD TO CART</span><span class="price">$200</span></div>
<div class="card" style="left:614px;top:686px"><div class="photo" role="img" aria-label="Mattress product photo"></div><span class="name">Product Name</span><span class="stars">★★★</span><span class="add">ADD TO CART</span><span class="price">$200</span></div>
<div class="card" style="left:843px;top:686px"><div class="photo" role="img" aria-label="Mattress product photo"></div><span class="name">Product Name</span><span class="stars">★★★</span><span class="add">ADD TO CART</span><span class="price">$200</span></div>

<h2 class="section-title" style="top:1012px">Brands</h2>
<svg class="abs" style="left:126px;top:1116px" width="22" height="34"><path d="M18 3L5 17l13 14" fill="none" stroke="#bbb" stroke-width="4"/></svg>
<svg class="abs" style="left:1048px;top:1116px" width="22" height="34"><path d="M4 3l13 14L4 31" fill="none" stroke="#bbb" stroke-width="4"/></svg>
<div class="brand-logo" style="left:192px;width:160px">Brodin SpineEase</div>
<div class="brand-logo" style="left:388px;width:186px">Whitcombe &amp; Lyle</div>
<div class="brand-logo" style="left:600px;width:190px">Pardue</div>
<div class="brand-logo" style="left:820px;width:170px">Kellard DreamLoft</div>

<h2 class="section-title" style="top:1266px">Products</h2>
<div class="tab active" style="top:1342px">King <svg width="16" height="20" style="margin-left:18px"><path d="M4 3l8 7-8 7" fill="none" stroke="#fff" stroke-width="2.5"/></svg></div>
<div class="tab" style="top:1408px">Queen</div>
<div class="tab" style="top:1475px">Twin</div>
<div class="tab" style="top:1542px">Single</div>

<div class="card sm" style="left:443px;top:1360px"><div class="photo" role="img" aria-label="Mattress product photo"></div><span class="name">Product Name</span><span class="stars">★★★</span><span class="add">ADD TO CART</span><span class="price">$200</span></div>
<div class="card sm" style="left:654px;top:1360px"><div class="photo" role="img" aria-label="Mattress product photo"></div><span class="name">Product Name</span><span class="stars">★★★</span><span class="add">ADD TO CART</span><span class="price">$200</span></div>
<div class="card sm" style="left:864px;top:1360px"><div class="photo" role="img" aria-label="Mattress product photo"></div><span class="name">Product Name</span><span class="stars">★★★</span><span class="add">ADD TO CART</span><span class="price">$200</span></div>

<div class="page" style="left:125px">&lt;</div>
<div class="page on" style="left:171px">1</div>
<div class="page" style="left:218px">2</div>
<div class="page" style="left:264px">3</div>
<div class="page" style="left:310px">4</div>
<div class="page" style="left:358px">5</div>
<div class="page" style="left:405px">&gt;</div>

<section class="abs features">
  <div class="feature" style="left:158px"><h4>SUSPENDISSE SED</h4><p>Aliquam dignissim porttitor tortor non fermen-<br>tum. Curabitur in magna lectus. Duis sed eros<br>diam. Lorem ipsum dolor sit amet, consectetur.</p></div>
  <div class="feature" style="left:462px"><h4>SUSPENDISSE SED</h4><p>Aliquam dignissim porttitor tortor non fermen-<br>tum. Curabitur in magna lectus. Duis sed eros<br>diam. Lorem ipsum dolor sit amet, consectetur.</p></div>
  <div class="feature" style="left:766px"><h4>SUSPENDISSE SED</h4><p>Aliquam dignissim porttitor tortor non fermen-<br>tum. Curabitur in magna lectus. Duis sed eros<br>diam. Lorem ipsum dolor sit amet, consectetur.</p></div>
</section>

<footer class="abs footer"></footer>
<h3 class="footer-title" style="left:180px;top:2026px;width:180px;text-align:center;line-height:24px;white-space:normal">SIGN UP TO OUR NEWSLETTER</h3>
<div class="field" style="top:2091px">Name:</div>
<div class="field" style="top:2125px">Email:</div>
<div class="abs submit">Submit</div>

<h3 class="footer-title" style="left:502px;top:2031px">Contact Us</h3>
<svg class="abs" style="left:472px;top:2076px" width="28" height="24"><path d="M14 2L2 13h4v9h6v-6h4v6h6v-9h4z" fill="#fff"/></svg>
<p class="contact-line" style="top:2070px">24517 sw Heron Glade<br>Ln, Miami FL<br>33189</p>
<svg class="abs" style="left:477px;top:2159px" width="18" height="24"><rect x="2" y="1" width="14" height="22" rx="2" fill="none" stroke="#fff" stroke-width="2.5"/></svg>
<p class="contact-line" style="top:2160px">(786)413-9067</p>
<svg class="abs" style="left:472px;top:2218px" width="28" height="18"><rect x="1" y="1" width="26" height="16" fill="none" stroke="#fff" stroke-width="2"/><path d="M1 1l13 10L27 1" fill="none" stroke="#fff" stroke-width="2"/></svg>
<p class="contact-line" style="top:2215px">info@coralslumberdepot.com</p>

<h3 class="footer-title" style="left:832px;top:2031px">Keep Connected</h3>
<div class="social" style="top:2074px"><i></i>Like us on Pagewall</div>
<div class="social" style="top:2107px"><i></i>Follow us on Chirpline</div>
<div class="social on" style="top:2141px"><i></i>Add us on Circlenet</div>
<div class="social" style="top:2175px"><i></i>Follow us on Workweave</div>
<div class="social" style="top:2208px"><i></i>Subscribe to our RSS</div>

<div class="abs bottombar">
  <span class="abs" style="left:276px;top:9px">Copyright © 2014 Coral Slumber Depot. All rights reserved.</span>
  <span class="abs" style="left:672px;top:9px;word-spacing:2px">Company Information &nbsp; | &nbsp; Privacy Policy &nbsp; | &nbsp; Terms &amp; Conditions</span>
</div>

</body>
</html>
```